Tolvik Commercial Cleaning is lookong for a new business card design.

A fresh new design that's professional and stylish. We need a serious upgrade to our business cards. I have included pictures of our existing ones. Our clients include professional individuals and business owners. We woupdblike something professional and upbeat. Please have fun and see what you come uo with.

Target Market(s)

Property managers, business owners, facility managers and other similar professionals

Industry/Entity Type

Janitorial

Contact Information for Business Card

Name, cell, office number, email, web address

Font styles to use
Sans Serif

Colors

Designer to choose colors to be used in the design.

Requirements
Must have
• please use the green color in our logo
Nice to have
• Bar code
Should not have
• Address

```html
<!DOCTYPE html>
<html lang="en">
<head>
<meta charset="utf-8">
<title>Tolvik Commercial Cleaning — Business Card</title>
<link href="https://fonts.googleapis.com/css2?family=Lato:wght@400;700;900&display=swap" rel="stylesheet">
<style>
  :root {
    --green-deep: #1c7a33;
    --green-mid: #3a9a52;
    --green-light: #62b574;
    --green-text: #2f9a48;
    --navy: #3a5c94;
    --title-blue: #4a6088;
    --ink: #2b2b2e;
    --card-light: #eceaee;
    --card-shade: #dcd9de;
    --white: #ffffff;
  }
  * { margin: 0; padding: 0; box-sizing: border-box; }
  html, body { width: 1200px; height: 734px; overflow: hidden; background: #f2f1f3; }
  .card {
    position: relative;
    width: 1200px;
    height: 734px;
    overflow: hidden;
    font-family: "Lato", Arial, sans-serif;
    background: linear-gradient(100deg, var(--card-shade) 0%, var(--card-light) 45%, var(--card-light) 100%);
  }
  .card-art { position: absolute; inset: 0; width: 100%; height: 100%; }
  .brand { position: absolute; left: 84px; top: 52px; color: var(--white); }
  .brand-name { font-weight: 900; font-size: 150px; line-height: 1; letter-spacing: -2px; }
  .brand-tagline { font-weight: 700; font-size: 32px; margin-top: 26px; letter-spacing: 0.5px; }
  .person { position: absolute; left: 80px; top: 518px; }
  .person-name { font-weight: 900; font-size: 58px; color: var(--green-text); line-height: 1; }
  .person-title { font-weight: 400; font-size: 32px; color: var(--title-blue); margin-top: 8px; }
  .contacts { position: absolute; right: 72px; top: 454px; list-style: none; }
  .contact { display: flex; justify-content: flex-end; align-items: center; height: 43px; font-size: 32px; color: var(--ink); }
  .contact-icon { width: 28px; height: 28px; margin-left: 18px; flex: none; }
</style>
</head>
<body>
<div class="card">
  <svg class="card-art" viewBox="0 0 1200 734" aria-hidden="true">
    <defs>
      <linearGradient id="headerGreen" x1="0" y1="0" x2="1" y2="0">
        <stop offset="0" stop-color="#62b574"/>
        <stop offset="0.45" stop-color="#1c7a33"/>
        <stop offset="0.75" stop-color="#2a8540"/>
        <stop offset="1" stop-color="#55a065"/>
      </linearGradient>
    </defs>
    <polygon class="header-band" fill="url(#headerGreen)" points="0,0 1200,0 1200,290 0,370"/>
    <polygon class="accent-stripe-green" fill="var(--green-mid)" points="0,386 1200,306 1200,316 0,396"/>
    <polygon class="accent-stripe-navy" fill="var(--navy)" points="0,404 1200,324 1200,338 0,418"/>
  </svg>

  <div class="brand">
    <div class="brand-name">Tolvik</div>
    <div class="brand-tagline">Commercial Cleaning</div>
  </div>

  <div class="person">
    <div class="person-name">MARCO DELVANE</div>
    <div class="person-title">Founder &amp; CEO</div>
  </div>

  <ul class="contacts">
    <li class="contact">(555) 318-4270
      <svg class="contact-icon" viewBox="0 0 24 24"><path fill="var(--green-text)" d="M6.6 10.8a15 15 0 0 0 6.6 6.6l2.2-2.2c.3-.3.7-.4 1-.2 1.1.4 2.3.6 3.6.6.6 0 1 .4 1 1V20c0 .6-.4 1-1 1A17 17 0 0 1 3 4c0-.6.4-1 1-1h3.5c.6 0 1 .4 1 1 0 1.3.2 2.5.6 3.6.1.3 0 .7-.2 1z"/></svg>
    </li>
    <li class="contact">(555) 318-4270
      <svg class="contact-icon" viewBox="0 0 24 24"><rect x="6" y="2" width="12" height="20" rx="2" fill="none" stroke="var(--green-text)" stroke-width="2"/><circle cx="12" cy="18" r="1.2" fill="var(--green-text)"/></svg>
    </li>
    <li class="contact">marco@tolvikcleaning.com
      <svg class="contact-icon" viewBox="0 0 24 24"><rect x="2" y="5" width="20" height="14" fill="var(--green-text)"/><path d="M2 5l10 8 10-8M2 19l7-7M22 19l-7-7" fill="none" stroke="var(--white)" stroke-width="1.4"/></svg>
    </li>
    <li class="contact">tolvikcleaning.com
      <svg class="contact-icon" viewBox="0 0 24 24"><circle cx="12" cy="12" r="10" fill="var(--green-text)"/><path d="M12 2v20M2 12h20M12 2c-4 4-4 16 0 20M12 2c4 4 4 16 0 20" fill="none" stroke="var(--white)" stroke-width="1.3"/></svg>
    </li>
  </ul>
</div>
</body>
</html>
```